Website Redesign - We Need Your Magic!

Hello we are looking for you to help us re-design a high end and professional website for a high-end private school.

Here is the current site: http://www.ferndalecrest.com/

NOTE THIS IS DESIGN ONLY, NO CODING :)

The image they want to portray is that of high quality sports and education, in a creative "un-stiff" way.

Menu Bar: Horizontal

Look and Feel:

Site Colors: Dark green and a Gold yellow (logos are attached)

This site will represent a school so the look must be clean, bold, and classy. The site must have a very clean user interface, with things easily recognizable. Think simple.

The site should be visually appealing! If you come to me with templates, or a ton of text you will be out.

This site should be outside the box, we do not want boring, we do not want status quo. This site should instill excitement, innovation, and athletics.

So the main points again are:

1. High-end and classy look, with creative feel
2. Simple and clear navigation style
3. To cover the Junior and High School - Ferndale Crest College Schools

Think outside the box. We look forward to seeing what you come up with!!

Thank you for helping us create an amazing site for the school!

Industry/Entity Type

School

```html
<!DOCTYPE html>
<html lang="en">
<head>
<meta charset="utf-8">
<title>Ferndale Crest College</title>
<link href="https://fonts.googleapis.com/css2?family=Arimo:ital,wght@0,400;0,700;1,400&family=Open+Sans:wght@600;700&display=swap" rel="stylesheet">
<style>
:root{
  --green:#1a2d10;
  --gold:#c9a230;
  --gold-light:#e0b83a;
  --ink:#1e1e1e;
  --panel:#f1f1f1;
  --panel-line:#d8d8d8;
  --footer:#2a2a2a;
  --footer-deep:#1c1c1c;
}
*{box-sizing:border-box;margin:0;padding:0}
html,body{width:847px;height:1200px;overflow:hidden;background:#fff}
body{position:relative;font-family:Arimo,Arial,sans-serif;color:var(--ink)}
.abs{position:absolute}

.brand-mark{left:94px;top:14px;width:98px;height:110px;display:flex;flex-direction:column;align-items:center;justify-content:center;gap:6px}
.brand-mark .dot{width:64px;height:64px;border-radius:50%;background:var(--green)}
.brand-mark .name{font-size:10px;font-weight:700;color:var(--green);text-align:center;line-height:1.2}
.site-title{left:206px;top:44px;font-size:26px;font-weight:700;color:var(--gold);letter-spacing:.5px;white-space:nowrap}
.tagline{left:207px;top:82px;font-size:13.5px;font-style:italic;color:#111;white-space:nowrap}

.search{left:607px;top:29px;width:159px;height:25px;display:flex}
.search .field{flex:1;background:#eee;border:1px solid #ddd;font-size:9px;color:#999;padding:8px 5px 0}
.search .go{width:35px;background:#111;color:#fff;font-size:13px;display:flex;align-items:center;justify-content:center;border-radius:0 3px 3px 0}
.contact{left:607px;font-size:12px;color:#111;display:flex;align-items:center;gap:8px;white-space:nowrap}
.contact.phone{top:86px}
.contact.mail{top:109px}

.nav{left:78px;top:138px;width:692px;height:34px;background:var(--green);border-radius:3px;display:flex;align-items:center;padding:0 10px}
.nav a{font-size:10px;color:#fff;text-decoration:none;white-space:nowrap;flex:1 1 auto;text-align:center;height:17px;line-height:17px;border-right:1px solid #33492a}
.nav a:last-child{border-right:none}
.nav a.current{flex:0 0 69px;background:var(--gold);color:#111;margin:0 12px 0 2px;border-right:none;height:22px;line-height:22px}

.hero{left:80px;top:178px;width:690px;height:269px;background:linear-gradient(120deg,#6b4a2a 0%,#3f7f86 35%,#b8896a 60%,#3b2a1e 100%)}
.hero .arrow{position:absolute;top:115px;width:27px;height:26px;background:#000;display:flex;align-items:center;justify-content:center}
.hero .arrow.prev{left:0}
.hero .arrow.next{right:0}
.hero .caption{position:absolute;left:190px;top:200px;width:474px;height:56px;background:rgba(18,18,14,.88);display:flex;align-items:center;padding-left:13px;font-family:"Open Sans",sans-serif;font-weight:700;color:#fff;font-size:14px;gap:6px;white-space:nowrap}
.hero .caption em{font-style:normal;color:var(--gold-light);font-size:22px;font-weight:600}

.main{left:80px;width:457px}
.main h2{font-size:18px;font-weight:700;color:var(--gold);margin-bottom:6px}
.main p{font-size:9.4px;line-height:14px;margin-bottom:14px;color:#222}
.welcome{top:468px}
.welcome p{padding-left:2px}
.welcome strong{color:var(--green)}
.head-title{left:80px;top:690px;font-size:16px;font-weight:700;color:var(--gold)}
.head-photo{left:80px;top:722px;width:102px;height:89px;border:3px solid #ddd;background:linear-gradient(160deg,#244a33,#6f7b5a 60%,#c7a98a)}
.head-intro{left:195px;top:722px;width:345px}
.head-intro p{font-size:9.2px;line-height:14px;margin-bottom:14px}
.head-rest{left:78px;top:833px;width:462px}
.head-rest p{font-size:9.2px;line-height:14px;margin-bottom:14px}

.signup{left:557px;top:473px;width:210px;height:108px;background:var(--green);border-radius:3px;padding:9px 11px;color:#fff}
.signup h3{font-size:19px;font-weight:700;letter-spacing:.3px;margin-bottom:5px}
.signup p{font-size:9px;line-height:13px;color:#e6e6e6}
.signup .row{display:flex;margin-top:7px;height:24px}
.signup .row .field{flex:1;background:#fff;font-size:8.5px;color:#999;padding:7px 6px 0}
.signup .row .go{width:33px;background:var(--gold);font-size:12px;display:flex;align-items:center;justify-content:center}

.panel{left:557px;width:210px;background:var(--panel);border:1px solid var(--panel-line);border-radius:3px;padding:10px 13px}
.panel h3{font-size:18.5px;font-weight:700;color:#222;margin-bottom:12px;letter-spacing:.3px}
.events{top:609px;height:193px}
.events li{list-style:none;position:relative;padding-left:17px;font-size:9.2px;line-height:13px;margin-bottom:16px}
.events li::before,.links li::before{content:"";position:absolute;left:0;top:3px;border-left:4px solid var(--gold);border-top:3.5px solid transparent;border-bottom:3.5px solid transparent}
.events a{color:var(--gold);text-decoration:none;font-size:8.5px;margin-left:8px}
.links{top:830px;height:192px}
.links h3{margin-bottom:6px}
.links li{list-style:none;position:relative;padding-left:11px;font-size:8.2px;height:30.5px;line-height:30px;border-bottom:1px solid #ddd;width:138px;white-space:nowrap}
.links li:last-child{border-bottom:none}
.links li::before{border-left-color:#111;top:11px}

.footer{left:0;top:1050px;width:847px;height:124px;background:var(--footer);color:#fff}
.footer .pin{position:absolute;left:78px;top:28px}
.footer .divider{position:absolute;top:16px;height:97px;border-left:1px dashed #555}
.footer .address{position:absolute;left:128px;top:39px;text-align:right;font-size:8.5px;line-height:13px}
.footer .address b{display:block;font-size:13px;font-family:"Open Sans",sans-serif;letter-spacing:.4px;margin-bottom:2px}
.footer .address a{color:#fff;display:inline-block;margin-top:5px;font-size:8px;text-decoration:underline}
.footer .follow{position:absolute;left:345px;top:39px;width:115px;text-align:center}
.footer .follow h4{font-size:13px;font-family:"Open Sans",sans-serif;letter-spacing:.6px;margin-bottom:11px}
.footer .social{display:flex;justify-content:center;gap:14px}
.footer .social span{display:flex;flex-direction:column;align-items:center;gap:2px;font-size:6.5px;color:#bbb}
.footer .social i{width:26px;height:26px;border-radius:50%;background:#4a6da8;border:2px solid #ddd}
.footer .badge{position:absolute;background:#6a6a6a;border-radius:4px}
.footer .school-mark{position:absolute;left:718px;top:38px;display:flex;flex-direction:column;align-items:center;gap:4px;font-size:8px;color:#ddd;width:60px;text-align:center}
.footer .school-mark i{width:38px;height:38px;border-radius:50%;background:#ddd}
.copyright{left:0;top:1174px;width:847px;height:26px;background:var(--footer-deep);color:#ccc;font-size:8.5px;text-align:center;line-height:26px}
</style>
</head>
<body>

<header>
  <div class="abs brand-mark"><span class="dot"></span><span class="name">Ferndale Crest</span></div>
  <div class="abs site-title">Ferndale Crest College</div>
  <div class="abs tagline">Rising Together in Learning, Culture, Sport &amp; Life</div>
  <div class="abs search"><span class="field">Search....</span><span class="go">GO</span></div>
  <div class="abs contact phone">
    <svg width="13" height="13" viewBox="0 0 24 24"><path fill="#1a2d10" d="M6.6 10.8a15.1 15.1 0 0 0 6.6 6.6l2.2-2.2a1 1 0 0 1 1-.25 11.4 11.4 0 0 0 3.6.6 1 1 0 0 1 1 1V20a1 1 0 0 1-1 1A17 17 0 0 1 3 4a1 1 0 0 1 1-1h3.5a1 1 0 0 1 1 1c0 1.25.2 2.45.6 3.6a1 1 0 0 1-.25 1z"/></svg>
    0770 123 456 / 0770 654 321
  </div>
  <div class="abs contact mail">
    <svg width="14" height="10" viewBox="0 0 14 10"><rect width="14" height="10" fill="var(--gold)"/><path d="M0 0l7 5.5L14 0" fill="none" stroke="#fff" stroke-width="1"/></svg>
    admin@ferndalecrest.com
  </div>
  <nav class="abs nav">
    <a class="current">HOME</a><a>ABOUT US</a><a>ACADEMICS</a><a>SPORTS</a><a>JOINING FERNDALE CREST</a><a>ABOUT US</a><a>CONTACT US</a>
  </nav>
</header>

<section class="abs hero" role="img" aria-label="Photo of a teacher helping young pupils with a classroom craft activity">
  <span class="arrow prev"><svg width="10" height="16" viewBox="0 0 10 16"><path d="M8 1L2 8l6 7" fill="none" stroke="#fff" stroke-width="1.6"/></svg></span>
  <span class="arrow next"><svg width="10" height="16" viewBox="0 0 10 16"><path d="M2 1l6 7-6 7" fill="none" stroke="#fff" stroke-width="1.6"/></svg></span>
  <div class="caption">Preparing Students For Success In A <em>Changing World.</em></div>
</section>

<main>
  <div class="abs main welcome">
    <h2>Welcome to Ferndale Crest College</h2>
    <p>Welcome to <strong>Ferndale Crest Group of Schools</strong> where our School Motto is ‘Unitas’ meaning Togetherness. We aim to work together in every aspect of School life, from academics to sport.</p>
    <p>Ferndale Crest College opened on 9th March 1987 and occupies 95 ha of land amidst the gentle slopes of the Ferndale Hills, 10km north of Oakvale. This location encourages focus on School life away from the distractions and hustle and bustle of the larger towns.</p>
    <p>The day scholars have the option of selected bus drop off points for parents to collect day scholars closer to home.</p>
    <p>Ferndale Crest College offers a wide range of academic subjects alongside a varied sport and extra-curricular program.</p>
  </div>

  <h2 class="abs head-title">Headmaster's Message</h2>
  <div class="abs head-photo" role="img" aria-label="Portrait photo of the headmaster"></div>
  <div class="abs head-intro">
    <p><strong>Welcome to Ferndale Crest College.&nbsp; Here at the College we aim to encourage each pupil to be a self-confident, well-rounded individual.</strong></p>
    <p>We aim to propel them to the highest level of achievement in both academics and extra-curricular activities to provide them with the life skills they will need when they leave the College and to prepare them to be of value to society.</p>
  </div>
  <div class="abs head-rest">
    <p>The College is a warm community which lives out high standards and is rightly proud of its achievements. We are a small enough School for each pupil to be known well, but large enough to offer a wide range of subjects and experience.</p>
    <p>Our Website covers many aspects of the College from how to apply for a place, to the curriculum and to much more.&nbsp; I hope you find it helpful and interesting.</p>
    <p style="margin-top:28px">Please visit and meet the pupils, the staff and see for yourself what Ferndale Crest College can offer your son or daughter.&nbsp; I look forward to welcoming you and your family to Ferndale Crest College.</p>
  </div>
</main>

<aside>
  <div class="abs signup">
    <h3>Email Sign Up</h3>
    <p>If you would like to be added to the list of parents that receive the School Newsletter,</p>
    <div class="row"><span class="field">Your Email Address</span><span class="go">GO</span></div>
  </div>
  <div class="abs panel events">
    <h3>Upcoming Events</h3>
    <ul>
      <li>Robotic competitions teach students how to make an impact <a>Read More...</a></li>
      <li>Robotic competitions teach students how to make an impact <a>Read More...</a></li>
      <li>Robotic competitions teach students how to make an impact <a>Read More...</a></li>
    </ul>
  </div>
  <div class="abs panel links">
    <h3>Important Links</h3>
    <ul>
      <li>School Calender</li>
      <li>Registration Form</li>
      <li>Sports Announcements</li>
      <li>2nd Term 2014 Termly Calendar</li>
      <li>Contact Us</li>
    </ul>
  </div>
</aside>

<footer class="abs footer">
  <svg class="pin" width="33" height="44" viewBox="0 0 33 44"><path d="M16.5 0A16.5 16.5 0 0 0 0 16.5C0 29 16.5 44 16.5 44S33 29 33 16.5A16.5 16.5 0 0 0 16.5 0z" fill="#e8902a"/><circle cx="16.5" cy="16" r="5" fill="var(--footer)"/></svg>
  <div class="address"><b>Ferndale Crest College</b>12 Elmwood Road,<br>Ferndale 4020<br><a>Click here to see the directions &gt;&gt;</a></div>
  <span class="divider" style="left:310px"></span>
  <div class="follow">
    <h4>Follow Us On:</h4>
    <div class="social"><span><i></i>Chatterly</span><span><i></i>Tweetloop</span></div>
  </div>
  <span class="divider" style="left:498px"></span>
  <span class="badge" style="left:535px;top:38px;width:72px;height:26px"></span>
  <span class="badge" style="left:625px;top:33px;width:74px;height:30px"></span>
  <span class="badge" style="left:527px;top:74px;width:88px;height:30px"></span>
  <span class="badge" style="left:625px;top:77px;width:76px;height:28px"></span>
  <div class="school-mark"><i></i>Ferndale Crest</div>
</footer>
<div class="abs copyright">Copyright © 2015 Ferndale Crest. All Rights Reserved.</div>

</body>
</html>
```